Executive Coaching and Spiritual Development Company needs a business card design.

We need a business card design for our company. We already have a logo that was created through Brightloom that we will submit and would like to see this work on black, blue and white backgrounds. Our personal information should be included as well. The design should communicate trust, spirituality, support and partnership.

Industry/Entity Type

Business

Colors
0255a3
33a6d7
ffffff
000000
474747

Requirements
Nice to have
• The colors offered here are just ideas--we are open to other suggestions, too.

```html
<!DOCTYPE html>
<html lang="en">
<head>
<meta charset="UTF-8">
<title>Vellmora Business Card</title>
<link href="https://fonts.googleapis.com/css2?family=Arvo:wght@400;700&family=Lato:wght@400;700;900&display=swap" rel="stylesheet">
<style>
  :root {
    --backdrop: #2b2b2b;
    --brand-blue: #0255a3;
    --brand-blue-light: #0a66c2;
    --brand-blue-deep: #014a8f;
    --ink: #0d1b2a;
    --ink-soft: #222222;
    --paper: #f4f4f4;
    --white: #ffffff;
  }
  * { margin: 0; padding: 0; box-sizing: border-box; }
  html, body {
    width: 1200px; height: 900px; overflow: hidden;
    background: var(--backdrop);
    font-family: "Lato", Arial, sans-serif;
  }
  .stage {
    position: relative; width: 1200px; height: 900px;
    display: flex; align-items: center; justify-content: center; gap: 60px;
  }
  .card {
    position: relative; width: 520px; height: 300px; overflow: hidden;
    box-shadow: 0 12px 30px rgba(0,0,0,.5);
  }

  /* Front */
  .card-front {
    background: radial-gradient(ellipse at 40% 45%, var(--brand-blue-light), var(--brand-blue-deep));
  }
  .front-lockup {
    position: absolute; left: 58px; top: 100px;
    display: flex; align-items: center; gap: 18px;
  }
  .mark-circle {
    flex: none; width: 78px; height: 78px; border-radius: 50%;
    border: 3px solid var(--white);
  }
  .front-name {
    font-family: "Arvo", Georgia, serif; font-weight: 400;
    font-size: 58px; color: var(--white); letter-spacing: .5px;
  }
  .front-tagline {
    position: absolute; left: 0; right: 0; bottom: 44px; text-align: center;
    font-size: 12px; letter-spacing: 3.5px; color: var(--ink);
  }

  /* Back */
  .card-back { background: var(--paper); }
  .back-bands { position: absolute; inset: 0; }
  .back-lockup {
    position: absolute; left: 60px; top: 62px;
    display: flex; align-items: center; gap: 14px;
  }
  .back-lockup .mark-circle { width: 74px; height: 74px; border: 2.5px solid var(--ink); }
  .back-name {
    font-family: "Arvo", Georgia, serif; font-weight: 400;
    font-size: 48px; color: var(--ink);
  }
  .contact {
    position: absolute; right: 30px; top: 150px; text-align: right;
  }
  .contact-address {
    font-weight: 900; font-size: 14px; line-height: 1.2; color: var(--brand-blue);
  }
  .contact-line {
    display: flex; justify-content: flex-end; align-items: center; gap: 8px;
    font-size: 13px; color: var(--ink-soft); margin-top: 8px;
  }
  .contact-line svg { width: 14px; height: 14px; flex: none; }
  .contact-web {
    font-weight: 900; font-size: 19px; color: var(--brand-blue); margin-top: 10px;
  }
  .person {
    position: absolute; left: 34px; bottom: 46px;
  }
  .person-name {
    font-weight: 900; font-size: 19px; color: var(--brand-blue); letter-spacing: .3px;
  }
  .person-role { font-weight: 700; font-size: 15px; color: var(--ink-soft); }
</style>
</head>
<body>
<main class="stage">
  <section class="card card-front" aria-label="Card front">
    <div class="front-lockup">
      <span class="mark-circle"></span>
      <span class="front-name">Vellmora</span>
    </div>
    <p class="front-tagline">YOUR SLOGAN / TAGLINE HERE</p>
  </section>

  <section class="card card-back" aria-label="Card back">
    <svg class="back-bands" viewBox="0 0 520 300" preserveAspectRatio="none" aria-hidden="true">
      <path d="M0 0 H320 Q300 0 290 10 Q280 20 250 20 H0 Z" fill="var(--brand-blue)"/>
      <path d="M520 265 V300 H150 Q165 300 175 290 Q185 280 215 280 H480 Q505 280 520 265 Z" fill="var(--brand-blue)"/>
    </svg>

    <div class="back-lockup">
      <span class="mark-circle"></span>
      <span class="back-name">Vellmora</span>
    </div>

    <div class="contact">
      <p class="contact-address">Arden Vale, Merriton,<br>Calvera 5182</p>
      <p class="contact-line">555-214-0387
        <svg viewBox="0 0 24 24" aria-hidden="true"><path fill="var(--brand-blue)" d="M6.6 10.8a15 15 0 0 0 6.6 6.6l2.2-2.2c.3-.3.7-.4 1-.2 1.1.4 2.3.6 3.6.6.6 0 1 .4 1 1V20c0 .6-.4 1-1 1A17 17 0 0 1 3 4c0-.6.4-1 1-1h3.5c.6 0 1 .4 1 1 0 1.3.2 2.5.6 3.6.1.3 0 .7-.2 1z"/></svg>
      </p>
      <p class="contact-line">info@vellmora.com
        <svg viewBox="0 0 24 24" aria-hidden="true"><rect x="2" y="5" width="20" height="14" fill="var(--brand-blue)"/><path d="M2 5l10 8 10-8" fill="none" stroke="var(--paper)" stroke-width="1.5"/></svg>
      </p>
      <p class="contact-web">www.vellmora.com</p>
    </div>

    <div class="person">
      <p class="person-name">MARCO LELAND</p>
      <p class="person-role">Managing Director</p>
    </div>
  </section>
</main>
</body>
</html>
```